Business Card Design (NEW FILES)

ATTENTION: New vector files are available. Please update your design to reflect/use the new (better resolution) logo images.

Seeking a unique and professional business card design for a commercial drone photography/videography business. The layout should feature
the logo (attached) and include the following information:
Owen Tarrick
614-502-7738
www.skylarkreelworks.example
NRD Certified Remote Pilot

Owen Tarrick

```html
<!DOCTYPE html>
<html lang="en">
<head>
<meta charset="utf-8">
<title>Skylark Reelworks – Business Card</title>
<link href="https://fonts.googleapis.com/css2?family=Montserrat:wght@400;500;800&display=swap" rel="stylesheet">
<style>
  :root {
    --backdrop: #b9b9b9;
    --card: #ffffff;
    --navy: #23214f;
    --orange: #ee8a45;
    --ink: #1c1c2a;
  }
  * { box-sizing: border-box; margin: 0; padding: 0; }
  html, body {
    width: 1200px; height: 900px; overflow: hidden;
    background: var(--backdrop);
    font-family: "Montserrat", Arial, sans-serif;
  }
  .stage { position: relative; width: 1200px; height: 900px; }
  .card {
    position: absolute; width: 700px; height: 400px;
    background: var(--card); border-radius: 26px;
  }
  .card--front { left: 250px; top: 40px; }
  .card--back  { left: 250px; top: 460px; }

  .brand {
    position: absolute; display: flex; align-items: center; gap: 16px;
    white-space: nowrap;
  }
  .card--front .brand { left: 50%; top: 50%; transform: translate(-50%, -50%); }
  .card--back .brand { left: 50%; top: 46px; transform: translateX(-50%); }

  .brand__dot {
    width: 34px; height: 34px; border-radius: 50%;
    background: var(--orange); flex: none;
  }
  .brand__name {
    display: flex; flex-direction: column;
    color: var(--navy); font-weight: 500; font-size: 44px;
    letter-spacing: 2px; line-height: 1.05; text-transform: uppercase;
  }

  .details {
    position: absolute; left: 90px; top: 186px;
    display: flex; align-items: center;
  }
  .person { text-align: right; padding-right: 24px; white-space: nowrap; }
  .person__name { color: var(--navy); font-weight: 800; font-size: 30px; }
  .person__title { color: var(--ink); font-size: 15px; margin-top: 2px; }
  .divider { width: 1.5px; height: 96px; background: var(--ink); }
  .contacts { list-style: none; padding-left: 24px; }
  .contacts li {
    display: flex; align-items: center; gap: 12px; white-space: nowrap;
    color: var(--ink); font-size: 16px; line-height: 30px;
  }
  .contacts svg { width: 16px; height: 16px; fill: var(--navy); flex: none; }

  .credential {
    position: absolute; left: 0; right: 0; bottom: 40px;
    text-align: center; color: var(--ink); font-size: 16px; letter-spacing: 0.4px;
  }
</style>
</head>
<body>
<main class="stage">
  <section class="card card--front" aria-label="Card front">
    <div class="brand">
      <span class="brand__dot"></span>
      <p class="brand__name"><span>Skylark</span><span>Reelworks</span></p>
    </div>
  </section>

  <section class="card card--back" aria-label="Card back">
    <div class="brand">
      <span class="brand__dot"></span>
      <p class="brand__name"><span>Skylark</span><span>Reelworks</span></p>
    </div>

    <div class="details">
      <div class="person">
        <p class="person__name">Owen Tarrick</p>
        <p class="person__title">Owner</p>
      </div>
      <div class="divider"></div>
      <ul class="contacts">
        <li>
          <svg viewBox="0 0 24 24" aria-hidden="true"><path d="M6.6 10.8a15.1 15.1 0 0 0 6.6 6.6l2.2-2.2a1 1 0 0 1 1-.25 11.4 11.4 0 0 0 3.6.57 1 1 0 0 1 1 1V20a1 1 0 0 1-1 1A17 17 0 0 1 3 4a1 1 0 0 1 1-1h3.5a1 1 0 0 1 1 1 11.4 11.4 0 0 0 .57 3.6 1 1 0 0 1-.25 1z"/></svg>
          614-502-7738
        </li>
        <li>
          <svg viewBox="0 0 24 24" aria-hidden="true"><path d="M2 5h20v14H2z M4 7v.5l8 5 8-5V7l-8 5z" fill-rule="evenodd"/></svg>
          info@skylarkreelworks.example
        </li>
        <li>
          <svg viewBox="0 0 24 24" aria-hidden="true"><path d="M12 2a10 10 0 1 0 0 20 10 10 0 0 0 0-20zm6.9 6h-3a15.6 15.6 0 0 0-1.4-3.6A8 8 0 0 1 18.9 8zM12 4a14 14 0 0 1 1.9 4h-3.8A14 14 0 0 1 12 4zM4.3 14a8 8 0 0 1 0-4h3.4a16 16 0 0 0 0 4zm.8 2h3a15.6 15.6 0 0 0 1.4 3.6A8 8 0 0 1 5.1 16zm3-8h-3a8 8 0 0 1 4.4-3.6A15.6 15.6 0 0 0 8.1 8zM12 20a14 14 0 0 1-1.9-4h3.8A14 14 0 0 1 12 20zm2.3-6H9.7a14.7 14.7 0 0 1 0-4h4.6a14.7 14.7 0 0 1 0 4zm.2 5.6a15.6 15.6 0 0 0 1.4-3.6h3a8 8 0 0 1-4.4 3.6zm1.8-5.6a16 16 0 0 0 0-4h3.4a8 8 0 0 1 0 4z"/></svg>
          www.skylarkreelworks.example
        </li>
      </ul>
    </div>

    <p class="credential">NRD Certified Remote Pilot Fully Insured</p>
  </section>
</main>
</body>
</html>
```